Business Card for my New Brokerage

Looking to get a business card design for my new Real Estate Brokerage.
I want it with Picture, Phone Number, Email, Website, Office Address
Name and Designation. Please add logo too.

Target Market(s)

Real Estate Investors or Home Buyers

Industry/Entity Type

Real Estate

Contact Information for Business Card

Name, Email, Phone Number, website, email, office address

Colors
EB3D1F
EC4F4E
F09395
F8D3D4
FCEDEE

Requirements
Must have
• Minimalistic, Clean, Modern, Photo
Nice to have
• White and Red Colors

```html
<!DOCTYPE html>
<html lang="en">
<head>
<meta charset="UTF-8">
<title>Ember Realty Co — Business Card</title>
<link rel="stylesheet" href="https://fonts.googleapis.com/css2?family=Montserrat:wght@600;800&family=Arimo:wght@400&display=swap">
<style>
  :root {
    --page-bg: #1c1c1c;
    --card-bg: #0b0b0b;
    --brand-red: #e3121b;
    --text-light: #e6e6e6;
    --divider: #2c2c2c;
    --photo-top: #3a3a3a;
    --photo-bottom: #222222;
  }
  * { box-sizing: border-box; margin: 0; padding: 0; }
  html, body { width: 1200px; height: 900px; overflow: hidden; }
  body {
    background: var(--page-bg);
    display: flex;
    flex-direction: column;
    align-items: center;
    justify-content: center;
    gap: 40px;
    font-family: "Arimo", Arial, sans-serif;
  }
  .card {
    width: 660px;
    height: 377px;
    background: var(--card-bg);
    position: relative;
    display: flex;
  }
  .brand-name {
    font-family: "Montserrat", sans-serif;
    font-weight: 600;
    color: var(--brand-red);
    line-height: 1;
    white-space: nowrap;
  }

  /* contact side */
  .brand-panel {
    width: 46%;
    display: flex;
    flex-direction: column;
    align-items: center;
    justify-content: center;
    gap: 22px;
    border-right: 1px solid var(--divider);
    margin: 40px 0;
  }
  .agent-photo {
    width: 120px;
    height: 120px;
    border-radius: 50%;
    background: linear-gradient(180deg, var(--photo-top), var(--photo-bottom));
  }
  .brand-panel .brand-name { font-size: 26px; letter-spacing: 1px; }
  .contact-panel {
    flex: 1;
    padding: 0 40px;
    display: flex;
    flex-direction: column;
    justify-content: center;
    color: var(--text-light);
  }
  .person-name {
    font-family: "Montserrat", sans-serif;
    font-weight: 800;
    color: var(--brand-red);
    font-size: 25px;
    letter-spacing: 0.5px;
  }
  .person-title { font-size: 17px; margin-top: 4px; margin-bottom: 18px; }
  .contact-list { list-style: none; }
  .contact-list li {
    display: flex; align-items: center; gap: 10px;
    font-size: 16px; margin-bottom: 6px;
  }
  .contact-list svg { width: 16px; height: 16px; flex: none; }
  .accent { color: var(--brand-red); }
  .address { font-size: 16px; margin-top: 18px; line-height: 1.35; padding-left: 26px; }

  /* logo side */
  .card-back { align-items: center; justify-content: center; }
  .card-back .brand-name { font-size: 40px; letter-spacing: 2px; }
</style>
</head>
<body>

<section class="card card-front">
  <div class="brand-panel">
    <div class="agent-photo" role="img" aria-label="Portrait photo of the agent"></div>
    <span class="brand-name">EMBER REALTY CO</span>
  </div>
  <div class="contact-panel">
    <h1 class="person-name">MARCUS HALE</h1>
    <p class="person-title">Managing Director</p>
    <ul class="contact-list">
      <li>
        <svg viewBox="0 0 24 24" aria-hidden="true"><path fill="#e3121b" d="M6.6 10.8a15 15 0 0 0 6.6 6.6l2.2-2.2a1 1 0 0 1 1-.25 11.4 11.4 0 0 0 3.6.57 1 1 0 0 1 1 1V20a1 1 0 0 1-1 1A17 17 0 0 1 3 4a1 1 0 0 1 1-1h3.5a1 1 0 0 1 1 1c0 1.25.2 2.45.57 3.57a1 1 0 0 1-.25 1z"/></svg>
        044-987 654 321
      </li>
      <li>
        <svg viewBox="0 0 24 24" aria-hidden="true"><rect x="2" y="5" width="20" height="14" fill="#e3121b"/><path d="M2 5l10 8 10-8" fill="none" stroke="#0b0b0b" stroke-width="1.8"/></svg>
        hello@emberhomes.com
      </li>
      <li>
        <svg viewBox="0 0 24 24" aria-hidden="true"><g fill="none" stroke="#e3121b" stroke-width="2"><circle cx="12" cy="12" r="9.5"/><ellipse cx="12" cy="12" rx="4" ry="9.5"/><path d="M2.5 12h19M4 7h16M4 17h16"/></g></svg>
        <span>www.<span class="accent">emberrealty</span>.com</span>
      </li>
    </ul>
    <p class="address">18 Harbor Lane, Suite 4<br>45210, Westland</p>
  </div>
</section>

<section class="card card-back">
  <span class="brand-name">EMBER REALTY CO</span>
</section>

</body>
</html>
```